Fashion Site

I need a Home Page and one Internal Page (About or Stores you choose) for a Fashion Retailer called ZELVA based in Melbourne Australia. Their product range is high end - European brand (i.e. Velto, Darnex etc) shoes, handbags and accessories for Women and Men (Customers 75% Women 25% Men). They currently have a site at www.zelva-store.com.au (My developer will take this design and push it through the rest of the site).

The new design will be clean and modern and reflect the high end brands they sell. The finished site will have the home page plus the following pages - About - Stores - News/Sales - E-Shop - Contact with links to Join our mail list - Chatterbook - Snapreel. I would like a main banner/slider at the top that will have 6 sliding images - through these images I would like to reinforce the following - the products are imported direct from Italy and are the latest most current designs from leading fashion houses (women and men) - A Modern Look with an Italian feel. Then we would also like to show some products/specials from the new E-Shop on the home page as well as the usual links etc.

Their colours are black and white but I am open to having a splash of colour and a must is to use the photography supplied in a creative way (see http://plumtorvel.com as an Idea), we want to show that the products are high end - hand made. Their end/tag line is Always In Fashion. We DO NOT want any brand names mentioned/Listed (if on a photo that is fine). The site will need to be easy to navigate and google friendly so please keep this in mind with the design. The images supplied include: Product Shots, Melbourne Stores, Italy Warehouse (2 story building with red roof) and Italy Factories/Craftsmen.

Target Market(s)

Fashion Conscious Women and Men who like the finer things in life

Industry/Entity Type

Fashion

Font styles to use
Serif
Sans Serif

Requirements
Must have
• Top Banner with 6 Images that Slide/Scroll in a banner.
Nice to have
• See the Following Sites that may inspire:
https://www.kivo.com.au
http://www.sundrapeq.co (the Look not the colours)
http://www.tolgaberry.com
Also Like the banner in this http://plumtorvel.com (Just the banner)

```html
<!DOCTYPE html>
<html lang="en">
<head>
<meta charset="utf-8">
<title>ZELVA – Always In Fashion</title>
<link rel="stylesheet" href="https://fonts.googleapis.com/css2?family=Bebas+Neue&family=Arimo:wght@400;700&display=swap">
<style>
  :root {
    --ink: #1a1a1a;
    --text: #333333;
    --muted: #8a8a8a;
    --page: #fdfdfd;
    --panel: #f4f4f4;
    --rule: #e6e6e6;
    --hatch: #ececec;
    --black: #000000;
    --white: #ffffff;
    --logo-box: #6e6e6e;
    --dot-off: #555555;
  }
  * { margin: 0; padding: 0; box-sizing: border-box; }
  html, body { width: 1143px; height: 1200px; overflow: hidden; }
  body {
    position: relative;
    background: var(--page);
    font-family: "Arimo", Arial, sans-serif;
    color: var(--text);
  }
  h2, h3 { font-weight: 400; }
  .top-rule { position: absolute; left: 0; top: 22px; width: 1143px; height: 5px; background: var(--rule); }
  .top-rule-marker { position: absolute; left: 488px; top: 27px; }

  .brand {
    position: absolute; left: 188px; top: 42px;
    font-family: "Bebas Neue", Impact, sans-serif;
    font-size: 80px; line-height: 1; color: var(--ink); letter-spacing: 1px;
  }

  .main-nav { position: absolute; top: 62px; left: 0; width: 1143px; }
  .nav-item {
    position: absolute; transform: translateX(-50%); text-align: center;
    font-family: "Bebas Neue", Impact, sans-serif; white-space: nowrap;
  }
  .nav-kicker { display: block; font-size: 10px; color: var(--muted); letter-spacing: .3px; }
  .nav-label { display: block; font-size: 22px; color: var(--ink); line-height: 1.05; }

  .hero-top { position: absolute; left: 188px; top: 135px; width: 767px; height: 72px; background: var(--black); }
  .hero-image {
    position: absolute; left: 188px; top: 207px; width: 767px; height: 319px;
    background: linear-gradient(90deg, #e9e9e7 0%, #d9d6d0 18%, #8a7f70 34%, #efefef 50%, #cfcfcf 68%, #9a9a9a 82%, #eeeeee 100%);
  }
  .hero-bar { position: absolute; left: 188px; top: 526px; width: 767px; height: 61px; background: var(--black); }
  .hero-badge {
    position: absolute; left: 0; top: 0; width: 98px; height: 61px; background: var(--logo-box);
    font-family: "Bebas Neue", Impact, sans-serif; font-size: 32px; color: var(--ink);
    display: flex; align-items: center; justify-content: center;
  }
  .slider-dots { position: absolute; right: 13px; top: 37px; display: flex; gap: 6px; }
  .slider-dots span { width: 19px; height: 4px; background: var(--white); }
  .slider-dots span.off { background: var(--dot-off); }
  .hero-pointer { position: absolute; left: 382px; top: 50px; }

  .intro {
    position: absolute; left: 188px; top: 587px; width: 767px; height: 78px; background: var(--panel);
    padding: 40px 12px 0 13px; font-size: 9.6px; line-height: 12px; color: var(--text);
  }

  .section-head { position: absolute; left: 188px; top: 698px; width: 767px; height: 23px; }
  .section-head .band { position: absolute; top: 0; height: 23px; background: var(--hatch); }
  .section-head .band.left { left: 0; width: 277px; }
  .section-head .band.right { right: 0; width: 279px; }
  .section-title {
    position: absolute; left: 0; width: 767px; top: 1px; text-align: center;
    font-family: "Bebas Neue", Impact, sans-serif; font-size: 19px; color: var(--ink);
  }

  .product { position: absolute; top: 764px; width: 179px; }
  .product-photo {
    height: 98px;
    background: linear-gradient(135deg, #f2f2f2 0%, #2f6fae 40%, #1e5a96 55%, #d9574a 75%, #f2f2f2 100%);
  }
  .product-name { margin-top: 13px; font-family: "Bebas Neue", Impact, sans-serif; font-size: 15px; line-height: 18px; color: var(--ink); padding-left: 3px; }
  .product-desc { margin-top: 4px; font-size: 9.6px; line-height: 14.6px; color: var(--text); }
  .product-link {
    margin-top: 5px; display: flex; align-items: center; gap: 10px; padding-left: 3px;
    font-family: "Bebas Neue", Impact, sans-serif; font-size: 13px; color: var(--ink);
  }

  .site-footer {
    position: absolute; left: 0; top: 1088px; width: 1143px; height: 100px; background: var(--panel);
    border-top: 1px dotted #dcdcdc;
  }
  .copyright { position: absolute; left: 190px; top: 33px; font-size: 9px; color: var(--muted); }
  .copyright strong { color: var(--text); font-weight: 400; }
  .social { position: absolute; left: 760px; top: 28px; display: flex; gap: 12px; }
  .social-link { display: flex; align-items: center; gap: 4px; font-size: 10px; color: var(--text); }
  .social-link i { width: 10px; height: 10px; background: var(--muted); display: block; }
</style>
</head>
<body>
  <div class="top-rule"></div>
  <svg class="top-rule-marker" width="16" height="8" viewBox="0 0 16 8"><path d="M0 0 L8 8 L16 0 Z" fill="#e6e6e6"/></svg>

  <header>
    <div class="brand">ZELVA</div>
    <nav class="main-nav">
      <div class="nav-item" style="left:409px"><span class="nav-kicker">Homepage</span><span class="nav-label">Home</span></div>
      <div class="nav-item" style="left:502px"><span class="nav-kicker">Who are we?</span><span class="nav-label">About</span></div>
      <div class="nav-item" style="left:609px"><span class="nav-kicker">Where to find us</span><span class="nav-label">Stores</span></div>
      <div class="nav-item" style="left:729px"><span class="nav-kicker">Latest news</span><span class="nav-label">News/Sales</span></div>
      <div class="nav-item" style="left:832px"><span class="nav-kicker">Where to buy</span><span class="nav-label">E-Shop</span></div>
      <div class="nav-item" style="left:924px"><span class="nav-kicker">Get in touch</span><span class="nav-label">Contact</span></div>
    </nav>
  </header>

  <section class="hero">
    <div class="hero-top"></div>
    <div class="hero-image" role="img" aria-label="Slider photo: two hanging leather sneakers, one brown and one white with black straps, on a white background"></div>
    <div class="hero-bar">
      <div class="hero-badge">ZELVA</div>
      <svg class="hero-pointer" width="16" height="11" viewBox="0 0 16 11"><path d="M0 11 L8 3 L16 11 Z" fill="#ffffff"/></svg>
      <div class="slider-dots"><span></span><span class="off"></span><span></span><span></span><span></span><span></span></div>
    </div>
  </section>

  <p class="intro">Lorem ipsum dolor sit amet, consectetur adipiscing elit. Vivamus non diam et lacus pulvinar venenatis et vestibulum velit. Pellentesque interdum faucibus dui hendrerit ultrices. Aliquam erat volutpat. Duis commodo turpis id diam pulvinar hendrerit.</p>

  <div class="section-head">
    <div class="band left"></div>
    <div class="band right"></div>
    <h2 class="section-title">Special Products This Month</h2>
  </div>

  <article class="product" style="left:188px">
    <div class="product-photo" role="img" aria-label="Product photo: blue and red leather loafers"></div>
    <h3 class="product-name">Corvino Mens</h3>
    <p class="product-desc">Maecenas ipsum metus, semper hendrerit varius mattis, congue sit amet tellus. Aliquam ullamcorper dui sed magna posue re ut elementum enim rutrum.</p>
    <div class="product-link"><svg width="12" height="8" viewBox="0 0 12 8"><path d="M0 0 L4 4 L0 8 M6 0 L10 4 L6 8" stroke="#1a1a1a" stroke-width="2" fill="none"/></svg>View Product</div>
  </article>
  <article class="product" style="left:384px">
    <div class="product-photo" role="img" aria-label="Product photo: blue and red leather loafers"></div>
    <h3 class="product-name">Corvino Mens</h3>
    <p class="product-desc">Maecenas ipsum metus, semper hendrerit varius mattis, congue sit amet tellus. Aliquam ullamcorper dui sed magna posue re ut elementum enim rutrum.</p>
    <div class="product-link"><svg width="12" height="8" viewBox="0 0 12 8"><path d="M0 0 L4 4 L0 8 M6 0 L10 4 L6 8" stroke="#1a1a1a" stroke-width="2" fill="none"/></svg>View Product</div>
  </article>
  <article class="product" style="left:580px">
    <div class="product-photo" role="img" aria-label="Product photo: blue and red leather loafers"></div>
    <h3 class="product-name">Corvino Mens</h3>
    <p class="product-desc">Maecenas ipsum metus, semper hendrerit varius mattis, congue sit amet tellus. Aliquam ullamcorper dui sed magna posue re ut elementum enim rutrum.</p>
    <div class="product-link"><svg width="12" height="8" viewBox="0 0 12 8"><path d="M0 0 L4 4 L0 8 M6 0 L10 4 L6 8" stroke="#1a1a1a" stroke-width="2" fill="none"/></svg>View Product</div>
  </article>
  <article class="product" style="left:776px">
    <div class="product-photo" role="img" aria-label="Product photo: blue and red leather loafers"></div>
    <h3 class="product-name">Corvino Mens</h3>
    <p class="product-desc">Maecenas ipsum metus, semper hendrerit varius mattis, congue sit amet tellus. Aliquam ullamcorper dui sed magna posue re ut elementum enim rutrum.</p>
    <div class="product-link"><svg width="12" height="8" viewBox="0 0 12 8"><path d="M0 0 L4 4 L0 8 M6 0 L10 4 L6 8" stroke="#1a1a1a" stroke-width="2" fill="none"/></svg>View Product</div>
  </article>

  <footer class="site-footer">
    <p class="copyright">All Content Copyright 2014- <strong>zelva</strong>. All Rights Reserved.</p>
    <div class="social">
      <span class="social-link"><i></i>Chatterbook</span>
      <span class="social-link"><i></i>Chirpline</span>
      <span class="social-link"><i></i>Feed</span>
    </div>
  </footer>
</body>
</html>
```